Northfield Sum Tutor

Need a new design for northfieldsumtutor.com as we are having a new backend developed. The design should be fun, and visually interesting for kids, yet sophisticated enough for parents, teachers and school districts.

Our main competitor is qvo.com and we like their concept. The colors should pop, and be exciting. The layout should be simple. Because we are having our website developed, we only will need the design and no functionality, a Photoshop or Fireworks file will work best.

We like the simplicity of our existing site, but it looks fairly unexciting. Here is a version our developers gave us. We do not like the design.

http://pelvonworks.com/pelvonlayout/northfieldsumtutor/layout/

The winning designer will most likely get more work from us as we make modifications.

Target Market(s)

Parents, Teachers, students

Industry/Entity Type

School

Requirements
Must have
• login at the top
social icons for recommend and like
Showcase area for features and testimonials

```html
<!DOCTYPE html>
<html lang="en">
<head>
<meta charset="utf-8">
<title>Northfield Sum Tutor</title>
<link href="https://fonts.googleapis.com/css2?family=Open+Sans:ital,wght@0,300;0,400;0,600;1,400&display=swap" rel="stylesheet">
<style>
:root{
  --sky-top:#72d6f2;
  --sky-bottom:#4aa6c6;
  --page:#efefef;
  --card:#ffffff;
  --panel:#ececec;
  --ink:#1e1e1e;
  --nav-ink:#1f7f98;
  --teal-dark:#2f93b3;
  --red-dark:#d3092d;
  --blue-btn:#4a8fd2;
  --line:#dcdcdc;
  --login-bg:#3cc2ea;
}
*{box-sizing:border-box;margin:0;padding:0}
html,body{width:1020px;height:1200px;overflow:hidden}
body{
  position:relative;
  font-family:"Open Sans",Arial,sans-serif;
  color:var(--ink);
  background:linear-gradient(to bottom,var(--sky-top) 0,var(--sky-bottom) 447px,var(--page) 447px);
}
.abs{position:absolute}
h1,h2{font-weight:inherit}

/* header */
.brand{left:20px;top:46px;display:flex;align-items:center;gap:6px;color:#fff;font-size:25px;font-weight:600}
.brand-dot{width:24px;height:24px;border-radius:50%;background:var(--red-dark)}
.login{left:519px;top:37px;width:481px;height:55px;background:var(--login-bg);border:1px solid #2aa9d4;border-radius:3px}
.login-title{position:absolute;left:13px;top:6px;font-size:19px;color:#0f5f7e}
.login-field{position:absolute;top:9px;width:155px;height:21px;background:#fff;border:1px solid #9fd6e8}
.login-btn{position:absolute;left:401px;top:8px;width:64px;height:22px;border:1px solid #a7a7a7;border-radius:2px;background:linear-gradient(#fdfdfd,#dcdcdc);font-size:13px;text-align:center;line-height:20px;color:#222}
.login-note{position:absolute;top:34px;font-size:11px;color:#1a6f8c;display:flex;align-items:center;gap:5px}
.check{width:8px;height:8px;background:#fff;border:1px solid #999}

/* card */
.card{left:20px;top:120px;width:980px;height:1016px;background:var(--card);border-radius:6px}
.nav{left:33px;top:135px;width:953px;height:44px;border:1px solid #d3d3d3;border-radius:5px;background:linear-gradient(#fafafa,#e9e9e9);display:flex;overflow:hidden}
.nav-item{height:100%;border-right:1px solid #d3d3d3;color:var(--nav-ink);font-size:16px;display:flex;align-items:center;justify-content:center}
.nav-item.is-active{background:linear-gradient(#62c6e2,#3da8c8);color:#0d4f66}
.btn-red{background:linear-gradient(#f53a5a,var(--red-dark));color:#fff;border-radius:5px;text-align:center}
.register{left:821px;top:142px;width:141px;height:30px;font-size:16px;line-height:30px}

/* hero */
.hero{left:33px;top:193px;width:955px;height:364px;background:var(--panel);border-radius:5px}
.hero-art{left:53px;top:210px;width:548px;height:301px;
  background:linear-gradient(100deg,#d9d7a2 0%,#c9c890 28%,#8a8d4f 48%,#5d6631 66%,#55602c 100%)}
.hero-title{left:634px;top:270px;font-size:31px;font-weight:400;letter-spacing:1px;color:#111;white-space:nowrap}
.hero-text{left:635px;top:316px;width:310px;font-size:15px;line-height:28px;color:#222}
.sample{left:782px;top:461px;width:158px;height:30px;font-size:16px;line-height:30px}
.dots{left:472px;top:533px;display:flex;gap:8px}
.dot{width:12px;height:12px;border-radius:50%;background:radial-gradient(circle at 40% 35%,#6cc8e6,#21809f)}
.dot.is-off{background:radial-gradient(circle at 40% 35%,#fff,#bbb);border:1px solid #888}

/* featured */
.feat-title{left:37px;top:585px;font-size:21px;font-weight:400;color:#222}
.rule{height:1px;background:var(--line)}
.feat-img{width:252px;height:97px;border-radius:6px}
.feat-text{width:250px;font-size:11.5px;line-height:16px;color:#222;letter-spacing:.2px}
.btn-teal{width:87px;height:24px;background:linear-gradient(#5cc0dc,var(--teal-dark));color:#fff;font-size:12px;line-height:24px;text-align:center}
.pager{top:1085px;width:30px;height:27px;background:#dedede;display:flex;align-items:center;justify-content:center}

/* testimonials */
.testi{left:640px;top:582px;width:347px;height:407px;border:1px solid #cfcfcf;border-radius:3px;background:linear-gradient(#fafafa,#e2e2e4);overflow:hidden}
.testi-head{height:38px;background:linear-gradient(#7fd2ea,#3ea9c9);font-size:21px;padding:6px 0 0 20px;color:#0c3b4d}
.quote{position:absolute;left:22px;width:303px;font-size:11.5px;line-height:16px;color:#222;border-bottom:1px solid #d0d0d0;padding-bottom:10px;padding-right:10px}
.quote-by{text-align:right;font-style:italic;font-size:13px;margin-top:4px;margin-right:-10px}
.btn-blue{position:absolute;left:239px;top:363px;width:87px;height:24px;background:linear-gradient(#67a7e2,var(--blue-btn));color:#fff;font-size:12px;line-height:24px;text-align:center}
.like-note{left:742px;top:1026px;font-size:12px;color:#222}
.like-btn{left:921px;top:1019px;width:62px;height:30px;border:1px solid #c9d4e6;border-radius:3px;background:linear-gradient(#fff,#e8eef7);font-size:13px;font-weight:600;color:#3b5b98;display:flex;align-items:center;justify-content:center;gap:4px}
.socials{left:717px;top:1078px;display:flex;gap:9px}
.social{width:30px;height:30px;border-radius:5px;display:flex;align-items:center;justify-content:center;box-shadow:inset 0 -2px 0 rgba(0,0,0,.15),0 1px 2px rgba(0,0,0,.2)}

.footer{left:20px;top:1162px;font-size:11.5px;color:#222}
</style>
</head>
<body>

<header>
  <div class="abs brand"><span class="brand-dot"></span>Northfield Sum Tutor</div>
  <form class="abs login">
    <span class="login-title">Login</span>
    <span class="login-field" style="left:78px"></span>
    <span class="login-field" style="left:240px"></span>
    <span class="login-btn">Login</span>
    <span class="login-note" style="left:80px"><span class="check"></span>Remember me</span>
    <span class="login-note" style="left:241px">Forgot my password?</span>
  </form>
</header>

<div class="abs card"></div>

<nav class="abs nav">
  <div class="nav-item is-active" style="width:111px">Home</div>
  <div class="nav-item" style="width:159px">About NST</div>
  <div class="nav-item" style="width:126px">Pricing</div>
  <div class="nav-item" style="width:200px">Learning Centers</div>
  <div class="nav-item" style="width:127px">Contact</div>
</nav>
<div class="abs btn-red register">Register Now</div>

<section>
  <div class="abs hero"></div>
  <div class="abs hero-art" role="img" aria-label="Cartoon owl teacher in a graduation cap pointing at a chalkboard showing 1+1=?"></div>
  <h1 class="abs hero-title">PRINTED EXERCISES</h1>
  <p class="abs hero-text">Hundreds of worksheets, download and print out exercise files for each course section and work the problems to under&shy;stand all the concepts.</p>
  <div class="abs btn-red sample">Print a Sample</div>
  <div class="abs dots"><span class="dot is-off"></span><span class="dot"></span><span class="dot"></span></div>
</section>

<section>
  <h2 class="abs feat-title">Featured Area</h2>
  <div class="abs rule" style="left:37px;top:618px;width:581px"></div>

  <div class="abs feat-img" style="left:39px;top:635px;background:linear-gradient(90deg,#3f6e55,#6b8f78 60%,#d9d6cf)" role="img" aria-label="Teacher at a chalkboard of multiplication tables with students raising hands"></div>
  <p class="abs feat-text" style="left:42px;top:743px">Lorem Ipsum is simply dummy text of the printing and typesetting industry. Lorem Ipsum has been the industry's standard dummy text .</p>
  <div class="abs btn-teal" style="left:41px;top:818px">Learn more</div>

  <div class="abs feat-img" style="left:351px;top:635px;background:linear-gradient(135deg,#3f4a5e,#55607a)" role="img" aria-label="Chalkboard with division and multiplication equations"></div>
  <p class="abs feat-text" style="left:355px;top:743px">Lorem Ipsum is simply dummy text of the printing and typesetting industry. Lorem Ipsum has been the industry's standard dummy text .</p>
  <div class="abs btn-teal" style="left:356px;top:818px">Learn more</div>

  <div class="abs feat-img" style="left:39px;top:864px;background:linear-gradient(135deg,#2f7a6e,#4f948a)" role="img" aria-label="Teacher writing a distance formula on a green chalkboard"></div>
  <p class="abs feat-text" style="left:42px;top:972px">Lorem Ipsum is simply dummy text of the printing and typesetting industry. Lorem Ipsum has been the industry's standard dummy text .</p>
  <div class="abs btn-teal" style="left:41px;top:1045px">Learn more</div>

  <div class="abs feat-img" style="left:351px;top:864px;background:linear-gradient(135deg,#6d7a52,#93a07a)" role="img" aria-label="Student thinking in front of a chalkboard of calculus formulas"></div>
  <p class="abs feat-text" style="left:355px;top:972px">Lorem Ipsum is simply dummy text of the printing and typesetting industry. Lorem Ipsum has been the industry's standard dummy text .</p>
  <div class="abs btn-teal" style="left:356px;top:1045px">Learn more</div>

  <div class="abs rule" style="left:37px;top:1084px;width:581px"></div>
  <div class="abs pager" style="left:550px"><svg width="10" height="14"><path d="M8 1 2 7l6 6" fill="none" stroke="#888" stroke-width="1.5"/></svg></div>
  <div class="abs pager" style="left:582px"><svg width="10" height="14"><path d="M2 1l6 6-6 6" fill="none" stroke="#888" stroke-width="1.5"/></svg></div>
</section>

<aside>
  <div class="abs testi">
    <div class="testi-head">Testimonials</div>
    <div class="quote" style="top:58px">If your kids are struggling in math, try this program. It works! Each lesson is thorough, and easy to under&shy;stand.<div class="quote-by">R. Dalton</div></div>
    <div class="quote" style="top:154px">If your kids are struggling in math, try this program. It works! Each lesson is thorough, and easy to under&shy;stand.<div class="quote-by">R. Dalton</div></div>
    <div class="quote" style="top:264px">If your kids are struggling in math, try this program. It works! Each lesson is thorough, and easy to under&shy;stand.<div class="quote-by">R. Dalton</div></div>
    <div class="btn-blue">Learn more</div>
  </div>
  <p class="abs like-note">Be the first to like this site</p>
  <div class="abs like-btn"><svg width="14" height="14"><path d="M1 6h3v7H1zM5 6l3-5c1 0 2 1 1.5 3L9 6h4l-1 7H5z" fill="#4a6ea9"/></svg>Like</div>
  <div class="abs socials" aria-label="Share links">
    <span class="social" style="background:linear-gradient(#5677b8,#3b5ea3)"><svg width="16" height="16"><circle cx="4" cy="8" r="2.3" fill="#fff"/><circle cx="12" cy="3.5" r="2.3" fill="#fff"/><circle cx="12" cy="12.5" r="2.3" fill="#fff"/><path d="M4 8 12 3.5M4 8l8 4.5" stroke="#fff" stroke-width="1.4"/></svg></span>
    <span class="social" style="background:linear-gradient(#3a7fc4,#1a5fa8)"><svg width="16" height="16"><path d="M2 3h12v8H7l-3 3v-3H2z" fill="#fff"/></svg></span>
    <span class="social" style="background:linear-gradient(#58b968,#39a24a)"><svg width="16" height="16"><path d="M8 1l2.1 4.4 4.8.6-3.5 3.3.9 4.7L8 11.7 3.7 14l.9-4.7L1.1 6l4.8-.6z" fill="#fff"/></svg></span>
    <span class="social" style="background:linear-gradient(#76ccef,#4fb8e6)"><svg width="16" height="16"><path d="M8 14S1.5 10 1.5 5.5A3.2 3.2 0 0 1 8 4a3.2 3.2 0 0 1 6.5 1.5C14.5 10 8 14 8 14z" fill="#fff"/></svg></span>
    <span class="social" style="background:linear-gradient(#4b8ddc,#2a6fc9)"><svg width="16" height="16"><path d="M4 1.5h8v13l-4-3-4 3z" fill="#fff"/></svg></span>
    <span class="social" style="background:linear-gradient(#4c9ccf,#2f82b8)"><svg width="16" height="16"><path d="M8 2v12M2 8h12" stroke="#fff" stroke-width="2.6"/></svg></span>
    <span class="social" style="background:linear-gradient(#a5b7d4,#8aa0c2)"><svg width="16" height="16"><path d="M6.5 9.5l3-3M5.5 7.5 4 9a2.1 2.1 0 0 0 3 3l1.5-1.5M10.5 8.5 12 7a2.1 2.1 0 0 0-3-3L7.5 5.5" fill="none" stroke="#fff" stroke-width="1.6" stroke-linecap="round"/></svg></span>
  </div>
</aside>

<footer class="abs footer">©2012 Northfield Sum Tutor - Terms of Service - Privacy Policy - Program Policies</footer>

</body>
</html>
```